Design a modern, classy & professional business card for an online real estate agency, specializing in medium-luxury properties in Thailand and later in Singapore and UK.

Possible design ideas so far: (not essential)

- curved corner(s) to the card, white on front & turquoise on back or visa versa.

- front of card - clear and simple, company name in metallic grey/monochrome, logo graphic & company name on front in spot UV or embossed/debossed effect.

- back of card - large, close-cropped, 'ghost' patterns of the C-shaped curves of logo, or company name repeated on back of card in spot UV.

Target Market(s)

- young to middle-aged professionals mainly (but ideally should design should suit all)

- UK, US,EU,AUS & ASIAN mainly (but ideally should design should suit all countries)

Industry/Entity Type

Real Estate

Requirements
Must have
• THEME:
- Luxurious & Modern
- Clean & striking
- Unique & creative

INFO:
- Logo & company name on front
- Contact details on back:

Tobias Hennlund
Managing Director

www.velmontestates.asia
www.velmontestates.co.uk

Tel: 083-274-6159
email: tobias@velmontestates.asia

(contact details can be displayed in any order as suites design.)

Nice to have
• - curved corner(s) to the card, white on front & turquoise on back or visa versa.

Should not have
• - No generic images of properties, palm trees/coconut trees etc.

- No other other bold colors, except for main turquoise, grey, metallic white & black theme.

- No obvious business card templates

```html
<!DOCTYPE html>
<html lang="en">
<head>
<meta charset="utf-8">
<title>Velmont Estates — Business Card</title>
<link href="https://fonts.googleapis.com/css2?family=Michroma&display=swap" rel="stylesheet">
<style>
  :root{
    --page:#ecebe8;
    --card-light:#ffffff;
    --card-shade:#e4e5e6;
    --turquoise:#2bbfc0;
    --grey-band:#7a7b7d;
    --grey-text:#6d6f72;
    --ink:#3c3d40;
    --rule:#8d8f92;
  }
  *{box-sizing:border-box;margin:0;padding:0}
  html,body{width:1057px;height:1200px;overflow:hidden}
  body{
    background:var(--page);
    font-family:"Michroma",sans-serif;
    display:flex;align-items:center;justify-content:center;gap:70px;
  }
  .card{
    position:relative;width:400px;height:700px;
    background:radial-gradient(ellipse at 55% 45%,var(--card-light) 0%,var(--card-light) 35%,var(--card-shade) 100%);
    box-shadow:0 14px 30px rgba(0,0,0,.18);
  }
  .brand{
    position:absolute;left:0;right:0;top:70px;
    display:flex;flex-direction:column;align-items:center;gap:18px;
  }
  .brand-square{width:66px;height:66px;background:var(--turquoise)}
  .brand-name{font-size:19px;color:var(--grey-text);letter-spacing:.5px;white-space:nowrap}

  /* front side */
  .card-front .side-band{
    position:absolute;top:0;right:0;bottom:0;width:34px;background:var(--grey-band);
  }
  .card-front .brand{right:34px}
  .contact{
    position:absolute;right:34px;left:20px;top:255px;
    display:flex;flex-direction:column;align-items:flex-end;
  }
  .person{text-align:right;padding-right:84px;margin-bottom:22px}
  .person-name{font-size:16px;color:var(--turquoise);letter-spacing:1px;white-space:nowrap}
  .person-title{font-size:8.5px;color:var(--turquoise);letter-spacing:1px;margin-top:4px}
  .info-group{display:flex;flex-direction:column;align-items:flex-end;margin-bottom:26px}
  .info-row{display:flex;align-items:flex-end;font-size:10px;color:var(--ink);line-height:1;white-space:nowrap}
  .info-row span{padding-bottom:5px}
  .info-row .rule{width:70px;height:1px;background:var(--rule);margin-left:12px}
  .info-row + .info-row{margin-top:9px}

  /* back side */
  .card-back .brand{top:120px}
  .web-line{
    position:absolute;left:26px;right:70px;bottom:74px;
    display:flex;align-items:center;gap:12px;
    font-size:10px;color:var(--ink);
    padding-bottom:8px;border-bottom:1px solid var(--turquoise);
  }
  .web-line svg{flex:none}
</style>
</head>
<body>

  <section class="card card-front" aria-label="Card front with contact details">
    <div class="brand">
      <div class="brand-square"></div>
      <div class="brand-name">Velmont Estates</div>
    </div>
    <div class="contact">
      <div class="person">
        <div class="person-name">TOBIAS HENNLUND</div>
        <div class="person-title">MANAGING DIRECTOR</div>
      </div>
      <div class="info-group">
        <div class="info-row"><span>Tel: 083-274-6159</span><i class="rule"></i></div>
        <div class="info-row"><span>email: tobias@velmontestates.asia</span><i class="rule"></i></div>
      </div>
      <div class="info-group">
        <div class="info-row"><span>www.velmontestates.asia</span><i class="rule"></i></div>
        <div class="info-row"><span>www.velmontestates.co.uk</span><i class="rule"></i></div>
      </div>
    </div>
    <div class="side-band"></div>
  </section>

  <section class="card card-back" aria-label="Card back with brand">
    <div class="brand">
      <div class="brand-square"></div>
      <div class="brand-name">Velmont Estates</div>
    </div>
    <div class="web-line">
      <svg width="18" height="18" viewBox="0 0 18 18" aria-hidden="true">
        <circle cx="9" cy="9" r="7.5" fill="none" stroke="var(--turquoise)" stroke-width="1.3"/>
        <ellipse cx="9" cy="9" rx="3.2" ry="7.5" fill="none" stroke="var(--turquoise)" stroke-width="1"/>
        <line x1="1.5" y1="9" x2="16.5" y2="9" stroke="var(--turquoise)" stroke-width="1"/>
      </svg>
      <span>www.velmontestates.asia</span>
    </div>
  </section>

</body>
</html>
```